Cruise Booking Website

Cruise search and booking website

This project is a redesign of a cruise booking website we did a few years ago.

The current website is located here: http://voyage.pylonworks.example/en/

It's not fully functional but gives you ad idea how miserable the old design was.

All the information about cruises, cruise lines, destinations, ports and shore excursions will be similar to http://www.sailquest.example/
Actual search pages (form, results, single result, sailing and cabin selection, ship info, booking) will have EXACTLY the same info as sailquest.example

We like the style of http://harborfleetdesk.example, it's quite modern, good spacing, not overloaded with information. So you can use it as an example of what we like, not what we want as a final result for us. Please, don't copy it. The result should not be possible to resemble the harborfleetdesk.example, because our site has to be unique. This is important!
If you submit a design that clearly reminds another cruise site it will be rejected!

Also the mockup provided is just to give you the basic structure and show what information has to be present on the page. It doesn't mean the layout has to be the same as a mockup. The layout is up to the designer.

I've updated the mockup to be more generic so it doesn't confuse you:
https://files.boxvault.example/s/k7m2qp9wz4hx/Home%20page.png

When you're adding social sharing icons like plazanet/chirpline you have to use chinese ones instead:
https://files.boxvault.example/s/t3nr8vx5lc2e/chinese-social-icons.png
Originals: http://minilk.example/qR7t

We'll start with home page first and after it's approved inner pages can be designed.

I know the cost of the project doesn't look high, but the task is straight forward and doesn't require to be very original, it's better to follow existing design and layout patterns that proved to work well.
That's why I encourage you to choose a template to build the design on top of one of https://themeparlor.example/ themes if it will save the design work, will be easier and faster for you. So it will be more like a customization than a new design from scratch.

Mockups, site map and logo files:
- https://files.boxvault.example/sh/h48dm2rs73fkpw/QvnbW2Xz8e

Website tree:
- https://sheets.papernest.example/document/d/7xPqR2mLw9sTk4VbN8cHj3YzA6eUf5GdKo1iMnBv/edit?usp=sharing
Updates

So far a lot of designs are just copying http://www.harborfleetdesk.example/ - we don't like it!

We like the style of harborfleetdesk.example, it's quite modern, good spacing, not overloaded with information. So you can use it as an example of what we like, not what we want as a final result for us. Please, don't copy it. The result should not be possible to resemble the harborfleetdesk.example, because our site has to be unique. This is important!

Target Market(s)

Chinese travellers

Industry/Entity Type

Build

Requirements
Must have
• * White, blue and red
* Large spacing, not too much information cramped into a small space like sailquest.example or the current website
* More "hidden" info in popups, tabs and so on, so not to many things are visible at the same time
* Compatible with kestrel scaffold styling (for easier coding):
- http://kestrelkit.codeshelf.example/scaffold/index.html
- http://skinmarket.example/
* Feel free to propose to build the design on top of one of https://themeparlor.example/ themes if it will save the design work, will be easier and faster for you

```html
<!DOCTYPE html>
<html lang="en">
<head>
<meta charset="utf-8">
<title>海途邮轮 – About Us</title>
<link href="https://fonts.googleapis.com/css2?family=Source+Sans+3:wght@400;600;700&display=swap" rel="stylesheet">
<style>
:root{
  --blue:#2a68a6;
  --nav-top:#1b93dc;
  --nav-bot:#0b64b2;
  --nav-active:#1aa7ef;
  --panel-grey:#5a5a5a;
  --box-grey:#eeeeee;
  --line-grey:#d8d8d8;
  --orange:#f7941d;
  --orange-light:#fbb040;
  --navy:#0d3a6a;
  --footer:#3e79b4;
  --footer-bar:#376fab;
  --white:#ffffff;
  --text:#333333;
}
*{box-sizing:border-box;margin:0;padding:0}
html,body{width:1137px;height:1200px;overflow:hidden}
body{font-family:"Source Sans 3",sans-serif;color:var(--text);background:#1e5a96}
.stage{position:absolute;left:0;top:0;width:1400px;height:1477px;transform:scale(.8121);transform-origin:0 0;
  background:radial-gradient(ellipse 55% 60% at 50% 45%,#e3edf6 0%,#8fb4da 35%,#3a76b2 65%,#1c5893 100%)}
.abs{position:absolute}
.column{position:absolute;left:210px;top:0;width:980px;height:1477px;background:var(--white)}
.brand{left:225px;top:38px;display:flex;align-items:center;gap:8px}
.brand-dot{width:54px;height:54px;border-radius:50%;background:var(--blue)}
.brand-name{font-size:42px;font-weight:700;color:var(--blue);line-height:1}
.brand-url{left:285px;top:84px;font-size:12px;font-weight:700;color:var(--blue);letter-spacing:.5px}
.account{left:927px;top:19px;font-size:13px;color:var(--blue)}
.account span{margin:0 10px;color:#999}
.social{left:1054px;top:16px;display:flex;gap:5px}
.social i{width:26px;height:26px;border-radius:5px;display:block}
.hotline-icon{left:741px;top:62px}
.hotline-num{left:787px;top:54px;font-size:23px;font-weight:700;color:var(--blue);line-height:28px}
.hotline-sub{left:787px;top:80px;font-size:18px;color:#444;line-height:24px}
.search{left:940px;top:76px;width:231px;height:27px;border:1px solid #ccc;border-radius:3px;background:#f7f7f7;font-size:10px;color:#777;padding:6px 11px}
.search svg{position:absolute;right:8px;top:6px}
.nav{left:210px;top:130px;width:980px;height:40px;background:linear-gradient(var(--nav-top),var(--nav-bot));display:flex}
.nav a{color:var(--white);font-size:12px;font-weight:700;text-decoration:none;line-height:40px;text-align:center;border-right:1px solid rgba(255,255,255,.18)}
.nav a.active{background:var(--nav-active)}
.crumb{left:238px;top:193px;font-size:12px;color:var(--blue)}
.crumb b{font-weight:400;color:#999;margin:0 8px}
.about{left:232px;top:228px;width:620px;height:571px;background:var(--box-grey);border:1px solid var(--line-grey)}
.about h1{position:absolute;left:21px;top:14px;font-size:29px;font-weight:700;color:var(--blue)}
.about p{position:absolute;left:19px;width:575px;font-size:11px;line-height:18px;color:#333}
.video{left:19px;top:138px;width:581px;height:354px;background:#222}
.video-scene{position:absolute;left:0;top:0;width:581px;height:326px;background:linear-gradient(160deg,#8fa9b8 0%,#6f8b99 40%,#b28a6e 70%,#5d6f78 100%)}
.video-play{position:absolute;left:272px;top:142px}
.video-bar{position:absolute;left:0;top:326px;width:581px;height:28px;background:#1b1b1b;border-top:2px solid #3a3a3a}
.video-time{position:absolute;left:82px;top:6px;font-size:10px;color:#ddd}
.section-title{font-size:18px;font-weight:700;color:var(--blue)}
.deals{left:232px;top:862px;width:620px;height:184px;background:var(--box-grey);border:1px solid var(--line-grey)}
.deal{position:absolute;top:17px;width:175px}
.deal-photo{width:175px;height:111px;background:linear-gradient(#2e7fc4 0%,#6aaee0 45%,#1f6fb5 60%,#0f5a9c 100%)}
.deal p{font-size:13px;color:var(--blue);margin-left:5px;line-height:19px}
.deal p:first-of-type{margin-top:8px}
.arrow{width:20px;height:20px;background:#ddd;border:1px solid #ccc;display:flex;align-items:center;justify-content:center}
.partner{top:1107px;width:145px;height:73px;border:1px solid #d8d8d8;background:var(--white);display:flex;align-items:center;justify-content:center}
.partner i{display:block;width:96px;height:22px;border-radius:11px}
.finder{left:883px;top:193px;width:288px;height:407px;background:var(--panel-grey);border-radius:3px;color:#eee}
.finder h2{position:absolute;left:26px;top:18px;font-size:26px;font-weight:400;color:var(--white)}
.finder hr{position:absolute;left:3px;top:55px;width:282px;border:0;border-top:1px solid #777}
.finder label{position:absolute;font-size:14px}
.field{position:absolute;height:27px;background:linear-gradient(#f4f4f4,#d6d6d6);border:1px solid #bbb;border-radius:3px;font-size:11px;color:#224;padding:6px 10px}
.field::after{content:"";position:absolute;right:0;top:0;width:22px;height:25px;border-left:1px solid #bbb}
.field svg{position:absolute;right:6px;top:6px;z-index:1}
.check{position:absolute;left:24px;top:320px;font-size:11px;display:flex;align-items:center;gap:4px}
.check i{width:14px;height:14px;background:#ddd;border-radius:2px;display:block}
.btn-search{position:absolute;left:23px;top:346px;width:245px;height:39px;background:linear-gradient(var(--orange-light),var(--orange));border:1px solid #e07f10;border-radius:3px;color:var(--white);font-size:18px;font-weight:600;text-align:center;line-height:37px}
.newsletter{left:883px;top:626px;width:288px;height:347px;border-radius:3px;background:linear-gradient(#4b9bd8,#1f5f9e)}
.nl-frame{position:absolute;left:13px;top:16px;width:263px;height:155px;background:var(--white);padding:6px}
.nl-photo{width:251px;height:143px;background:linear-gradient(#6fc3e8 0%,#3aa6d8 45%,#e8eef2 65%,#9ec6de 100%)}
.newsletter h3{position:absolute;left:23px;top:183px;font-size:15px;font-weight:700;color:var(--white)}
.nl-sub{position:absolute;left:23px;top:210px;font-size:11px;color:var(--white)}
.nl-email{position:absolute;left:23px;top:238px;width:251px;height:26px;background:var(--white);border:1px solid #ccc;border-radius:2px;font-size:11px;color:#777;padding:5px 55px}
.nl-btn{position:absolute;left:24px;top:278px;width:102px;height:27px;background:var(--navy);color:var(--white);font-size:12px;text-align:center;line-height:27px;border-radius:2px}
.nl-rules{position:absolute;left:27px;top:313px;font-size:13px;color:var(--white)}
.footer{left:210px;top:1205px;width:980px;height:223px;background:var(--footer);color:var(--white)}
.footer-bar{left:210px;top:1428px;width:980px;height:49px;background:var(--footer-bar);color:var(--white);font-size:11px;text-align:center;line-height:49px}
.footer h4{position:absolute;font-size:16px;font-weight:700}
.footer ul{position:absolute;list-style:none;font-size:11px;line-height:22px}
.f-logo{position:absolute;left:405px;top:74px;width:99px;height:97px;background:var(--white);display:flex;flex-direction:column;align-items:center;justify-content:center;gap:6px}
.f-logo i{width:38px;height:38px;border-radius:50%;background:var(--blue);display:block}
.f-logo span{font-size:13px;font-weight:700;color:var(--blue)}
.f-about{position:absolute;left:524px;top:80px;width:120px;font-size:13px;line-height:18px}
.f-addr{position:absolute;left:706px;top:66px;font-size:14px;line-height:19px}
.f-line{position:absolute;left:706px;font-size:13px;display:flex;align-items:center;gap:7px}
</style>
</head>
<body>
<div class="stage">
  <div class="column"></div>

  <header>
    <div class="abs brand"><span class="brand-dot"></span><span class="brand-name">海途邮轮</span></div>
    <div class="abs brand-url">www.haitucruise.example</div>
    <div class="abs account">Sign in<span>|</span>Signup</div>
    <div class="abs social" aria-label="Social sharing">
      <i style="background:#e6322b"></i><i style="background:#2aa4e0"></i><i style="background:#f39c12"></i><i style="background:#e33b3b"></i>
    </div>
    <svg class="abs hotline-icon" width="38" height="38" viewBox="0 0 38 38"><circle cx="19" cy="19" r="17" fill="none" stroke="#999" stroke-width="2"/><path d="M13 10c2-1 4 3 3 5-1 1-2 1-1 3 1 2 3 4 5 5 2 1 2 0 3-1 2-1 6 1 5 3-1 3-4 4-7 3-5-2-9-6-11-11-1-3 1-6 3-7z" fill="#777"/></svg>
    <div class="abs hotline-num">400 818 818</div>
    <div class="abs hotline-sub">Call Us Today!</div>
    <div class="abs search">SEARCH :
      <svg width="14" height="14" viewBox="0 0 14 14"><circle cx="6" cy="6" r="4.5" fill="none" stroke="#aaa" stroke-width="1.5"/><path d="M9.5 9.5l3.5 3.5" stroke="#aaa" stroke-width="1.5"/></svg>
    </div>
  </header>

  <nav class="abs nav">
    <a class="active" style="width:101px">HOME</a>
    <a style="width:141px">DESTINATIONS</a>
    <a style="width:124px">CRUISE LINES</a>
    <a style="width:131px">CRUISE INFO</a>
    <a style="width:93px">DEALS</a>
    <a style="width:155px">ONLINE BOOKING</a>
    <a style="width:125px">CONTACT US</a>
    <a style="width:110px;border-right:0">BLOG</a>
  </nav>

  <div class="abs crumb">HOME<b>›</b>ABOUT US</div>

  <section class="abs about">
    <h1>ABOUT US</h1>
    <p style="top:60px">Lorem Ipsum is simply dummy text of the printing and typesetting industry. Lorem Ipsum has been the industry's standard dummy text ever since the 1500s, when an unknown printer took a galley of type and scrambled it to make a type specimen book. It has survived not only five centuries, but also the leap into electronic typesetting.</p>
    <div class="abs video">
      <div class="video-scene" role="img" aria-label="Video still of happy friends on holiday under a blue sky"></div>
      <svg class="video-play" width="48" height="48" viewBox="0 0 48 48"><circle cx="24" cy="24" r="23" fill="rgba(40,40,40,.55)" stroke="rgba(255,255,255,.4)" stroke-width="2"/><path d="M18 14l16 10-16 10z" fill="#eee"/></svg>
      <div class="video-bar">
        <svg class="abs" style="left:18px;top:7px" width="14" height="14"><rect x="1" y="1" width="4" height="12" fill="#ccc"/><rect x="8" y="1" width="4" height="12" fill="#ccc"/></svg>
        <svg class="abs" style="left:52px;top:7px" width="20" height="14"><path d="M1 5h4l5-4v12l-5-4H1z" fill="#ccc"/><path d="M13 4q3 3 0 6" stroke="#ccc" fill="none"/></svg>
        <div class="video-time">0:00:00 / 2:22:25</div>
        <svg class="abs" style="left:450px;top:6px" width="124" height="16"><circle cx="8" cy="8" r="5" fill="none" stroke="#ccc" stroke-width="2"/><circle cx="35" cy="8" r="4" fill="#ccc"/><rect x="55" y="4" width="13" height="8" fill="none" stroke="#eee" stroke-width="2"/><rect x="80" y="3" width="16" height="10" fill="none" stroke="#ccc" stroke-width="1.5"/><path d="M106 6V2h4M116 2h4v4M120 10v4h-4M110 14h-4v-4" stroke="#ccc" fill="none" stroke-width="1.5"/></svg>
      </div>
    </div>
    <p style="top:514px">Lorem Ipsum is simply dummy text of the printing and typesetting industry. Lorem Ipsum has been the industry's standard dummy text ever since the 1500s, when an unknown printer took a galley of type and scrambled...</p>
  </section>

  <h2 class="abs section-title" style="left:233px;top:824px">LAST MINUTE DEALS</h2>
  <section class="abs deals">
    <div class="abs arrow" style="left:0;top:85px"><svg width="8" height="10"><path d="M6 1L2 5l4 4" stroke="#888" fill="none" stroke-width="1.5"/></svg></div>
    <div class="deal" style="left:26px"><div class="deal-photo" role="img" aria-label="White cruise ship on the open sea"></div><p>3 days Bahamas</p><p>From 9000</p></div>
    <div class="deal" style="left:221px"><div class="deal-photo" role="img" aria-label="Cruise ship sailing past a green island"></div><p>3 days Bahamas</p><p>From 9000</p></div>
    <div class="deal" style="left:416px"><div class="deal-photo" role="img" aria-label="Cruise ship in a harbour near a bridge"></div><p>3 days Bahamas</p><p>From 9000</p></div>
    <div class="abs arrow" style="left:599px;top:85px"><svg width="8" height="10"><path d="M2 1l4 4-4 4" stroke="#888" fill="none" stroke-width="1.5"/></svg></div>
  </section>

  <h2 class="abs section-title" style="left:228px;top:1070px">OUR RELIABLE PARTNERS</h2>
  <div class="abs arrow" style="left:1127px;top:1072px"><svg width="8" height="10"><path d="M6 1L2 5l4 4" stroke="#888" fill="none" stroke-width="1.5"/></svg></div>
  <div class="abs arrow" style="left:1151px;top:1072px"><svg width="8" height="10"><path d="M2 1l4 4-4 4" stroke="#888" fill="none" stroke-width="1.5"/></svg></div>
  <div class="abs partner" style="left:229px"><i style="background:#c9302c"></i></div>
  <div class="abs partner" style="left:389px"><i style="background:#1b4d9c"></i></div>
  <div class="abs partner" style="left:549px"><i style="background:#4a5a6a"></i></div>
  <div class="abs partner" style="left:709px"><i style="background:#f39c12"></i></div>
  <div class="abs partner" style="left:869px"><i style="background:#3a9ad9"></i></div>
  <div class="abs partner" style="left:1029px"><i style="background:#2a78c8"></i></div>

  <aside class="abs finder">
    <h2>Find Your Cruise</h2>
    <hr>
    <label style="left:24px;top:67px">Destination</label>
    <div class="field" style="left:23px;top:87px;width:239px">Destination name<svg width="10" height="14"><path d="M2 5l3-3 3 3M2 9l3 3 3-3" stroke="#666" fill="none"/></svg></div>
    <label style="left:24px;top:121px">Length</label>
    <label style="left:154px;top:121px">Month</label>
    <div class="field" style="left:23px;top:141px;width:109px">Length Area</div>
    <div class="field" style="left:154px;top:141px;width:108px"><svg width="10" height="14"><path d="M2 5l3-3 3 3M2 9l3 3 3-3" stroke="#666" fill="none"/></svg></div>
    <label style="left:22px;top:177px">Cruise Lines</label>
    <div class="field" style="left:21px;top:197px;width:243px">Any Cruise line<svg width="10" height="14"><path d="M2 5l3-3 3 3M2 9l3 3 3-3" stroke="#666" fill="none"/></svg></div>
    <label style="left:22px;top:238px;font-size:16px">Number of Travelers</label>
    <label style="left:24px;top:264px">Age 25+</label>
    <label style="left:153px;top:264px">Age 0 to 24</label>
    <div class="field" style="left:23px;top:284px;width:108px">5<svg width="10" height="14"><path d="M2 5l3-3 3 3M2 9l3 3 3-3" stroke="#666" fill="none"/></svg></div>
    <div class="field" style="left:153px;top:284px;width:108px">0<svg width="10" height="14"><path d="M2 5l3-3 3 3M2 9l3 3 3-3" stroke="#666" fill="none"/></svg></div>
    <div class="check"><i></i>Check for senior rates</div>
    <div class="btn-search">Search Cruises</div>
  </aside>

  <aside class="abs newsletter">
    <div class="nl-frame"><div class="nl-photo" role="img" aria-label="Senior couple relaxing on loungers by a pool"></div></div>
    <h3>Cruise Deals Newsletter</h3>
    <div class="nl-sub">Subscribe to the best Cruise deals Now!</div>
    <div class="nl-email">Email :</div>
    <div class="nl-btn">Subscribe</div>
    <div class="nl-rules">Contest Rules</div>
  </aside>

  <footer class="abs footer">
    <h4 style="left:32px;top:30px">Useful Pages</h4>
    <ul style="left:32px;top:57px"><li>About Us</li><li>Contact us</li><li>Blog</li><li>FAQ</li><li>Terms of Service</li><li>Payment info</li><li>Reward Points</li></ul>
    <h4 style="left:222px;top:30px">Cruise Infov</h4>
    <ul style="left:224px;top:56px"><li>Cruise news</li><li>Visa</li><li>Honeymoon cruises</li><li>Firsttime on a Cruise</li></ul>
    <h4 style="left:405px;top:37px;font-size:15px">About haitucruise.example</h4>
    <div class="f-logo"><i></i><span>海途邮轮</span></div>
    <div class="f-about">We're the most advanced cruise booking providr in china.</div>
    <h4 style="left:705px;top:37px;font-size:15px">Contact Us</h4>
    <div class="f-addr">Meridian Studio,Pte Ltd<br>Lakeside Centre x118, Harbor Ave 3.2<br>Coralport 20817 Bayland</div>
    <div class="f-line" style="top:134px"><svg width="16" height="12"><path d="M1 5q7-6 14 0l-2 2-3-1V4H6v2L3 7z M4 8h8l1 3H3z" fill="#fff"/></svg>(555) 014-2290 - (555) 017-3341</div>
    <div class="f-line" style="top:159px"><svg width="16" height="12"><rect x="1" y="1" width="14" height="10" fill="#fff"/><path d="M1 1l7 6 7-6" stroke="#3e79b4" fill="none"/></svg>mail@haitucruise.example</div>
  </footer>
  <div class="abs footer-bar">© 2013. haitucruise. All rights reserved.</div>
</div>
</body>
</html>
```